Brivolt Technologies business card design

We need a business card designed with our new logo. it would be great if the card could communicate it is a technology based company.

Target Market(s)

system integrators

Industry/Entity Type

technology, IOT

Contact Information for Business Card

Name, designation, Address, telephone number, email address

Requirements
Must have
• logo and company name
Nice to have
• something to do with technology

```html
<!DOCTYPE html>
<html lang="en">
<head>
<meta charset="utf-8">
<title>Brivolt Technologies – Business Card</title>
<link rel="stylesheet" href="https://fonts.googleapis.com/css2?family=Roboto:wght@400;700&display=swap">
<style>
  :root {
    --page-bg: #ffffff;
    --card-bg: #ffffff;
    --ink: #3d3d3f;
    --accent: #f7941d;
    --text: #222222;
    --shadow: rgba(0, 0, 0, 0.28);
  }
  * { box-sizing: border-box; margin: 0; padding: 0; }
  html, body {
    width: 1200px; height: 896px; overflow: hidden;
    background: var(--page-bg);
    font-family: "Roboto", Arial, sans-serif;
  }
  .canvas { position: relative; width: 1200px; height: 896px; }

  .card {
    position: absolute; left: 335px; width: 530px; height: 303px;
    background: var(--card-bg); border-radius: 36px;
    box-shadow: -3px 3px 7px var(--shadow);
  }
  .card--front { top: 125px; }
  .card--back { top: 473px; }

  /* wordmark */
  .wordmark {
    position: absolute; display: flex; align-items: center; gap: 16px;
    color: var(--ink); font-weight: 700;
  }
  .wordmark__square { background: var(--accent); flex: none; }
  .wordmark__text { display: flex; flex-direction: column; line-height: 1; }
  .wordmark__name { letter-spacing: 1px; }
  .wordmark__sub { letter-spacing: 9px; }

  .card--front .wordmark { left: 70px; top: 44px; }
  .card--front .wordmark__square { width: 44px; height: 44px; }
  .card--front .wordmark__name { font-size: 64px; }
  .card--front .wordmark__sub { font-size: 22px; margin-top: 8px; letter-spacing: 10px; }

  .card--back .wordmark { left: 52px; top: 95px; }
  .card--back .wordmark__square { width: 50px; height: 50px; }
  .card--back .wordmark__name { font-size: 70px; }
  .card--back .wordmark__sub { font-size: 24px; margin-top: 8px; letter-spacing: 11px; }

  /* person */
  .person__name {
    position: absolute; left: 0; right: 0; top: 176px;
    text-align: center; color: var(--accent);
    font-size: 22px; font-weight: 400;
  }
  .person__rule {
    position: absolute; left: 20px; right: 20px; top: 201px;
    display: flex; align-items: center; gap: 6px;
  }
  .person__rule::before, .person__rule::after {
    content: ""; flex: 1; height: 1.5px; background: var(--accent);
  }
  .person__title { font-size: 12.5px; color: var(--text); }

  /* contacts */
  .contacts {
    position: absolute; left: 20px; top: 222px;
    list-style: none; font-size: 12.5px; color: var(--text);
  }
  .contacts li { display: flex; align-items: center; gap: 3px; height: 20px; }
  .contacts svg { width: 11px; height: 11px; fill: var(--accent); }

  .address {
    position: absolute; right: 22px; top: 244px;
    text-align: right; font-size: 12.5px; line-height: 20.5px;
    color: var(--text); font-style: normal;
  }
</style>
</head>
<body>
<div class="canvas">

  <section class="card card--front">
    <div class="wordmark">
      <span class="wordmark__square"></span>
      <div class="wordmark__text">
        <span class="wordmark__name">BRIVOLT</span>
        <span class="wordmark__sub">TECHNOLOGIES</span>
      </div>
    </div>

    <h1 class="person__name">DANIEL REYES</h1>
    <div class="person__rule"><span class="person__title">Managing Director</span></div>

    <ul class="contacts">
      <li>
        <svg viewBox="0 0 24 24" aria-hidden="true"><path d="M6.6 10.8a15 15 0 0 0 6.6 6.6l2.2-2.2c.3-.3.7-.4 1-.2 1.1.4 2.3.6 3.6.6.6 0 1 .4 1 1V20c0 .6-.4 1-1 1A17 17 0 0 1 3 4c0-.6.4-1 1-1h3.5c.6 0 1 .4 1 1 0 1.3.2 2.5.6 3.6.1.3 0 .7-.2 1z"/></svg>
        123 456 789
      </li>
      <li>
        <svg viewBox="0 0 24 24" aria-hidden="true"><path d="M2 5h20v2l-10 6L2 7z M2 9l10 6 10-6v10H2z"/></svg>
        info@yourmail.com
      </li>
      <li>
        <svg viewBox="0 0 24 24" aria-hidden="true"><path d="M12 2a10 10 0 1 0 0 20 10 10 0 0 0 0-20zm-1 17.9A8 8 0 0 1 4.2 10.2L9 15v1a2 2 0 0 0 2 2zm6.9-2.5A2 2 0 0 0 16 16h-1v-3a1 1 0 0 0-1-1H8v-2h2a1 1 0 0 0 1-1V7h2a2 2 0 0 0 2-2v-.4a8 8 0 0 1 2.9 12.8z"/></svg>
        www.yourwebsite.com
      </li>
    </ul>

    <address class="address">
      1850 Harborview Lane<br>
      Seacliff CA 92631
    </address>
  </section>

  <section class="card card--back">
    <div class="wordmark">
      <span class="wordmark__square"></span>
      <div class="wordmark__text">
        <span class="wordmark__name">BRIVOLT</span>
        <span class="wordmark__sub">TECHNOLOGIES</span>
      </div>
    </div>
  </section>

</div>
</body>
</html>
```